Hardcore nerd needs to stand out in a sea of dull Defence business cards

Wombarra Devices is a new Australian consulting engineering company that turns research and theory into practical systems. No evangelistic fluff, just mathematics and physics into electronic and optical circuits for consumer products, scientific research or Defence applications.

We already have a recognised logo (provided) which is often dark blue/black on a light background but we're open to other combinations. (Us engineers tend to have limited aesthetic imagination :)

Some of our recent products have included:
* Instrumentation for electrical testing,
* Radar jammers,
* GPS antenna design,
* Satellite tracking systems,
* High power lasers

We're open to both single and double-sided designs - happy to be convinced either way.

P.S. Another group is working on the web page, so - alas - our web site is currently of no use for images/ideas...

Target Market(s)

Engineering managers,
Scientists

Contact Information for Business Card

Dr Colin Harte
R&D Engineer

colin@wombarradevices.com.au
0427 563 710

PO Box XXX (to be confirmed)
Kelsby ACT 2917
Australia

Font styles to use
Serif
Sans Serif

Colors

Designer to choose colors to be used in the design.

Requirements
Must have
• My contact details!
• I've had many (great) "bold and plain" designs submitted already, so feel free to be artistically creative :)
• Happy to take advice re fonts/colours/printability etc.
Nice to have
• I'm not sure if "lists" are more at home on a CV than a business card, but representative services include:
• Applied electromagnetics
• RF and high speed electronics
• Signal and image processing
• Electro-optical and laser systems
• Concept-to-prototype design services
• If you're considering double sided cards, then often measuring/alignment grids/rulers feature on the back of similar cards.
• e.g. https://www.veltranoptics.example/newgrouppage9.cfm?objectgroup_id=4183
• https://www.veltranoptics.example/newgrouppage9.cfm?objectgroup_ID=4185
• ..or even a "Smith chart" (google will return lots)
• Generic images to represent a capability might work - googling images associated with keyword for each of these areas might help:
• - "passive radar", "phased array", "fdtd", "vircator"
• RF and high speed electronic design
• - "smith chart", "microstrip circuits", "dimensioned drawing", "electronic schematic"
• - "dft", "iir filter"
• - "optical cavity". "laser energy level diagram"
• Background/watermarked images outlines/wireframes/schematics would probably look OK.
Should not have
• If a list of projects/services is provided, it is important not to make the client feel that this is "all" the company can do. Engineering design is a creative discipline (like graphics :)
• Please, no stock "military" snaps like planes, missiles, etc!

```html
<!DOCTYPE html>
<html lang="en">
<head>
<meta charset="utf-8">
<title>Wombarra Devices – Business Card</title>
<link href="https://fonts.googleapis.com/css2?family=Roboto:wght@400;500;700;900&display=swap" rel="stylesheet">
<style>
  :root {
    --navy: #1f2a63;
    --white: #ffffff;
    --stage: #2b2b2d;
    --soft: #d9dcea;
  }
  * { margin: 0; padding: 0; box-sizing: border-box; }
  html, body {
    width: 1200px; height: 839px; overflow: hidden;
    background: var(--stage);
    font-family: "Roboto", Arial, sans-serif;
  }
  .stage {
    position: relative; width: 1200px; height: 839px;
    display: flex; justify-content: center; align-items: center; gap: 90px;
  }
  .card {
    position: relative; width: 400px; height: 700px;
    border-radius: 28px; overflow: hidden;
    background: var(--navy);
  }
  /* Front */
  .card-front .top-panel {
    position: absolute; left: 0; top: 0; width: 100%; height: 330px;
    background: var(--white);
  }
  .wordmark {
    position: absolute; left: 0; width: 100%; text-align: center;
    font-weight: 900; letter-spacing: 1px; line-height: 1.05;
    text-transform: uppercase;
  }
  .card-front .wordmark {
    top: 62px; color: var(--navy); font-size: 46px;
  }
  .card-front .wordmark span { display: block; font-size: 26px; letter-spacing: 9px; }
  .mark-circle {
    position: absolute; border-radius: 50%;
  }
  .card-front .mark-circle {
    left: 125px; top: 215px; width: 150px; height: 150px;
    background: var(--navy); border: 10px solid var(--white);
  }
  .contact {
    position: absolute; left: 0; top: 400px; width: 100%;
    text-align: center; color: var(--white);
  }
  .person-name { font-size: 29px; font-weight: 700; letter-spacing: .5px; }
  .person-role { font-size: 17px; font-weight: 400; margin-top: 2px; }
  .icon-row { display: flex; justify-content: center; gap: 16px; margin: 20px 0 18px; }
  .icon-row svg { width: 28px; height: 28px; }
  .details { font-size: 17px; line-height: 1.4; }
  .divider { width: 80px; height: 3px; background: var(--white); margin: 18px auto; }
  .address { font-size: 17px; line-height: 1.4; }
  /* Back */
  .card-back .brand-lockup {
    position: absolute; left: 0; top: 290px; width: 100%;
    display: flex; align-items: center; justify-content: center; gap: 16px;
  }
  .card-back .mark-circle {
    position: static; width: 90px; height: 90px; background: var(--white);
  }
  .card-back .wordmark {
    position: static; width: auto; text-align: left;
    color: var(--white); font-size: 34px;
  }
  .card-back .wordmark span { display: block; font-size: 18px; letter-spacing: 6px; }
</style>
</head>
<body>
<main class="stage">
  <section class="card card-front" aria-label="Business card front">
    <div class="top-panel"></div>
    <div class="wordmark">Wombarra<span>Devices</span></div>
    <div class="mark-circle"></div>
    <div class="contact">
      <p class="person-name">DR COLIN HARTE</p>
      <p class="person-role">R&amp;D Engineer</p>
      <div class="icon-row">
        <svg viewBox="0 0 28 28" aria-label="phone"><circle cx="14" cy="14" r="14" fill="#fff"/><path d="M10 8c1 0 2 2.5 2 3s-1 1-1 1.5 2 3.5 4 4.5c.5 0 1-1 1.5-1s3 1 3 2-1.5 2.5-3 2.5C12 20 8 15 8 11c0-1.5 1-3 2-3z" fill="var(--navy)"/></svg>
        <svg viewBox="0 0 28 28" aria-label="email"><circle cx="14" cy="14" r="14" fill="#fff"/><rect x="7" y="9" width="14" height="10" rx="1.5" fill="var(--navy)"/><path d="M7.5 10l6.5 5 6.5-5" stroke="#fff" stroke-width="1.4" fill="none"/></svg>
        <svg viewBox="0 0 28 28" aria-label="website"><circle cx="14" cy="14" r="14" fill="#fff"/><circle cx="14" cy="14" r="7" fill="none" stroke="var(--navy)" stroke-width="1.5"/><ellipse cx="14" cy="14" rx="3" ry="7" fill="none" stroke="var(--navy)" stroke-width="1.3"/><path d="M7 14h14M8 10.5h12M8 17.5h12" stroke="var(--navy)" stroke-width="1.2"/></svg>
      </div>
      <div class="details">
        <p>0427 563 710</p>
        <p>colin@wombarradevices.com.au</p>
        <p>www.wombarradevices.com.au</p>
      </div>
      <div class="divider"></div>
      <div class="address">
        <p>PO Box XXX (to be confirmed)</p>
        <p>Kelsby ACT 2917, Australia</p>
      </div>
    </div>
  </section>

  <section class="card card-back" aria-label="Business card back">
    <div class="brand-lockup">
      <div class="mark-circle"></div>
      <div class="wordmark">Wombarra<span>Devices</span></div>
    </div>
  </section>
</main>
</body>
</html>
```